Oil Field Service company needs professional business cards

Looking to clean up our current company business cards and look a little more professional. Brenwick Casing Services is a US based company that services the oil field. We deal with engineers, managers and oil rigs....................................................................................................................................................................................................................................................................................................................................................................................................

Target Market(s)

Oil and Gas professionals

Industry/Entity Type

Oil And Gas

Contact Information for Business Card

See attached photo as example

Font styles to use
Sans Serif

Colors
ec1f27

Requirements
Must have
• Company Logo, Name, Title, Cell, Office, Fax, Email.
• See attached photo
Nice to have
• External CRT, Internal CRT, Casing Crews, Torque Turn, Laydown Machine
Should not have
• Do not introduce any new pictures and keep it professional looking

```html
<!DOCTYPE html>
<html lang="en">
<head>
<meta charset="utf-8">
<title>Brenwick Casing Services – Business Card</title>
<link href="https://fonts.googleapis.com/css2?family=Archivo:wght@700;800&family=Roboto:wght@400&family=Roboto+Condensed:wght@400&display=swap" rel="stylesheet">
<style>
  :root{
    --page:#e6e6e6;
    --slate:#3d5263;
    --paper:#fbfbfb;
    --ink:#34383c;
    --muted:#555a5e;
    --red:#ec1f27;
    --light:#e8e8e8;
  }
  *{margin:0;padding:0;box-sizing:border-box}
  html,body{width:1200px;height:576px;overflow:hidden;background:var(--page)}
  .canvas{position:relative;width:1200px;height:576px}
  .card{position:absolute;top:139px;width:484px;height:292px;border-radius:7px;box-shadow:0 2px 5px rgba(0,0,0,.22)}
  .card--front{left:82px;background:var(--slate)}
  .card--back{left:602px;background:var(--paper)}

  .wordmark{position:absolute;text-align:center;font-family:"Archivo",sans-serif;font-weight:800;text-transform:uppercase;line-height:1}
  .wordmark__name{display:block}
  .wordmark__sub{display:block;letter-spacing:.14em}
  .card--front .wordmark{left:0;right:0;top:108px;color:var(--light)}
  .card--front .wordmark__name{font-size:44px;letter-spacing:.01em}
  .card--front .wordmark__sub{font-size:14px;margin-top:12px}
  .card--back .wordmark{right:22px;top:200px;width:220px;color:var(--slate)}
  .card--back .wordmark__name{font-size:30px}
  .card--back .wordmark__sub{font-size:10.5px;margin-top:9px}

  .person{position:absolute;left:23px;top:38px}
  .person__name{font-family:"Archivo",sans-serif;font-weight:800;font-size:20.5px;color:var(--ink);letter-spacing:.01em;text-transform:uppercase}
  .person__title{font-family:"Roboto",sans-serif;font-size:11.5px;color:var(--muted);margin-top:2px}

  .contacts{position:absolute;left:23px;top:106px;list-style:none;font-family:"Roboto Condensed",sans-serif;font-size:12px;color:var(--ink)}
  .contacts li{display:flex;align-items:center;height:15.8px}
  .contacts svg{width:9px;height:9px;margin-right:12px;fill:var(--red);flex:none}
  .contacts .accent{color:var(--red)}
</style>
</head>
<body>
<div class="canvas">
  <section class="card card--front">
    <div class="wordmark">
      <span class="wordmark__name">Brenwick</span>
      <span class="wordmark__sub">Casing Services</span>
    </div>
  </section>

  <section class="card card--back">
    <div class="person">
      <h1 class="person__name">Cody Hallbrook</h1>
      <p class="person__title">Area Manager</p>
    </div>

    <ul class="contacts">
      <li><svg viewBox="0 0 10 10"><path d="M2 0.5 3.6 2.6 2.7 3.6C3.3 5 4.9 6.6 6.4 7.3L7.4 6.4 9.5 8 8.4 9.5C4.5 9 1 5.5.5 1.6Z"/></svg>(580) 555-0142</li>
      <li><svg viewBox="0 0 10 10"><path d="M0 3C2-.3 8-.3 10 3L8 4 7 2.5H3L2 4ZM2 5H8L9.5 9.5H.5Z"/></svg>(580) 555-0178</li>
      <li><svg viewBox="0 0 10 10"><path d="M2.5 0H7.5V3H2.5ZM0 3.5H10V8H8V6H2V8H0ZM2.5 6.5H7.5V10H2.5Z"/></svg>(580) 555-0193</li>
      <li><svg viewBox="0 0 10 10"><path d="M5 0C2.8 0 1.2 1.6 1.2 3.7 1.2 6.4 5 10 5 10S8.8 6.4 8.8 3.7C8.8 1.6 7.2 0 5 0ZM5 2.3A1.4 1.4 0 1 1 5 5.1 1.4 1.4 0 0 1 5 2.3Z"/></svg>Carrow, OK 73850</li>
      <li><svg viewBox="0 0 10 10"><path d="M0 1.5H10V2.5L5 5.8 0 2.5ZM0 3.7 5 7 10 3.7V8.5H0Z"/></svg>codyhallbrook@brenwicksrvs.com</li>
      <li><svg viewBox="0 0 10 10"><path d="M5 0A5 5 0 1 0 5 10 5 5 0 0 0 5 0ZM1.1 4.4H3C3.1 3 3.4 1.8 3.9 1.2 2.4 1.6 1.3 2.9 1.1 4.4ZM4 4.4H6C5.9 2.8 5.5 1.3 5 1 4.5 1.3 4.1 2.8 4 4.4ZM7 4.4H8.9C8.7 2.9 7.6 1.6 6.1 1.2 6.6 1.8 6.9 3 7 4.4ZM1.1 5.6C1.3 7.1 2.4 8.4 3.9 8.8 3.4 8.2 3.1 7 3 5.6ZM4 5.6C4.1 7.2 4.5 8.7 5 9 5.5 8.7 5.9 7.2 6 5.6ZM7 5.6C6.9 7 6.6 8.2 6.1 8.8 7.6 8.4 8.7 7.1 8.9 5.6Z"/></svg>www.<span class="accent">brenwicksrvs</span>.com</li>
    </ul>

    <div class="wordmark">
      <span class="wordmark__name">Brenwick</span>
      <span class="wordmark__sub">Casing Services</span>
    </div>
  </section>
</div>
</body>
</html>
```